Mobile Friendly Lead Generation Landing Page

We are a web marketing company that specialized in web lead generation. Recently we have started buying media from mobile devices and we need a mobile interface(landing page) where we can collect user data in an effective manner.

Our current mobile landing page is:
http://www.tutorpath.example.com/lp13d/index.aspx?a=true&source=841356
Through this you can see what the steps/questions users need to answer to get matched to a school. We need the design for the whole process.

We are pretty open for design ideas and our goal is to make this mobile optimized landing page have the look and feel of an app...but not an app.
There are several questions in the process but we are open to changing the way they are presented. As in, you can have one question at a time or a few.
The goal is to make this EXTREMELY EASY for users to interact with.

One example that we have liked is:
http://learnvane.example/schools/57214-page1.lvne (please note that this opens only on mobile devices)

Some of these screenshots are attached.

Our web form looks like this:
http://www.tutorpath.example.com/lp88/index.aspx?a=true

```html
<!DOCTYPE html>
<html lang="en">
<head>
<meta charset="utf-8">
<title>TutorPath App – Main Screen &amp; Form Screens</title>
<link rel="stylesheet" href="https://fonts.googleapis.com/css2?family=Roboto:wght@300;400;500;700&display=swap">
<style>
:root{
  --page-light:#f7f3f4;
  --page-edge:#e7dcdf;
  --ink:#1b1b1b;
  --ribbon:#ef1443;
  --chrome:#1ea1f1;
  --chrome-pill:#7ccdfb;
  --sky-top:#bfe3f8;
  --sky-mid:#e6eef0;
  --grass:#9cc436;
  --grass-deep:#7fb02a;
  --green:#05c47a;
  --red:#e8133a;
  --blue:#0a8cf5;
  --orange:#ff5a00;
  --navy:#0e5c9e;
  --headline:#1a5fa8;
  --select:#1c1722;
  --row:rgba(255,255,255,.42);
  --row-line:rgba(255,255,255,.7);
  --white:#ffffff;
}
*{box-sizing:border-box;margin:0;padding:0}
html,body{width:1200px;height:1000px;overflow:hidden}
body{
  position:relative;
  font-family:"Roboto",Helvetica,Arial,sans-serif;
  color:var(--ink);
  background:radial-gradient(ellipse at 50% 50%,var(--page-light) 0%,var(--page-edge) 100%);
}
.ribbon{position:absolute;left:0;top:0;width:170px;height:150px}
.page-title{position:absolute;top:52px;width:100%;text-align:center;font-size:64px;font-weight:400;letter-spacing:-.5px}
.caption{position:absolute;top:855px;width:100%;text-align:center}
.caption h2{font-size:48px;font-weight:400;letter-spacing:-.3px;line-height:56px}
.caption p{font-size:36px;font-weight:300;line-height:44px;margin-top:2px}

.screen{position:absolute;top:221px;width:320px;height:568px;overflow:hidden;
  background:linear-gradient(180deg,var(--sky-top) 10%,var(--sky-mid) 38%,var(--grass) 78%,var(--grass-deep) 100%)}
.screen--main{left:37px}
.screen--q1{left:440px}
.screen--q2{left:842px}

.status-bar{position:absolute;top:0;left:0;width:320px;height:22px;background:var(--chrome);color:var(--white);font-size:11px;line-height:22px}
.status-bar .carrier{position:absolute;left:6px}
.status-bar .time{position:absolute;left:0;width:100%;text-align:center}
.status-bar .battery{position:absolute;right:6px;display:flex;align-items:center;gap:3px}
.status-bar .battery i{display:inline-block;width:22px;height:9px;border:1px solid var(--white);background:var(--white);border-radius:2px}
.url-bar{position:absolute;top:22px;left:0;width:320px;height:42px;background:var(--chrome)}
.url-pill{position:absolute;top:2px;left:10px;width:300px;height:28px;border-radius:5px;background:var(--chrome-pill);color:var(--white);font-size:15px;line-height:28px;text-align:center}
.url-pill svg{position:absolute;right:8px;top:6px}
.toolbar{position:absolute;bottom:0;left:0;width:320px;height:44px;background:var(--chrome);display:flex;justify-content:space-around;align-items:center;padding:0 6px}

.grant-avatar{position:absolute;left:10px;top:75px;width:72px;height:72px;border-radius:50%;background:radial-gradient(circle,#f4c38a 0 30%,#6c7a3a 31% 55%,#1f3e7a 56%);border:3px solid #0f2a5c;z-index:2}
.grant-banner{position:absolute;left:80px;top:88px;width:230px;height:45px;background:var(--ribbon);color:var(--white);font-size:11px;line-height:18px;padding:4px 0 0 16px}
.promo{position:absolute;top:156px;width:100%;text-align:center;font-size:20px;color:var(--headline)}
.promo b{font-weight:700}
.area-head{position:absolute;left:10px;top:205px;width:300px;height:44px;background:var(--green);color:var(--white);font-size:16px;line-height:44px;padding-left:22px}
.area-list{position:absolute;left:10px;top:249px;width:300px;list-style:none}
.area-list li{height:44px;background:var(--row);border-bottom:1px solid var(--row-line);display:flex;align-items:center;font-size:12.5px;position:relative}
.area-list .icon{width:30px;height:30px;border-radius:50%;background:var(--navy);margin:0 10px 0 8px;display:flex;align-items:center;justify-content:center}
.area-list .chev{position:absolute;right:16px;top:15px}

.progress{position:absolute;left:10px;top:96px;display:flex;gap:11px}
.progress span{width:41px;height:14px;border:1.5px solid var(--orange);background:var(--white)}
.progress span.done{background:var(--orange)}
.question{position:absolute;left:10px;top:146px;width:300px;height:87px;background:var(--green);color:var(--white);font-size:17px;line-height:22px;text-align:center;display:flex;align-items:center;justify-content:center}
.options{position:absolute;left:10px;top:233px;width:300px;list-style:none}
.options li{height:44px;background:var(--row);border-bottom:1px solid var(--row-line);display:flex;align-items:center;font-size:15px}
.radio{width:17px;height:17px;border-radius:50%;border:1.5px solid var(--blue);background:var(--white);margin:0 10px 0 26px;display:flex;align-items:center;justify-content:center}
.radio.on::after{content:"";width:10px;height:10px;border-radius:50%;background:var(--blue)}
.year-select{position:absolute;left:10px;top:344px;width:300px;height:44px;background:var(--select);color:var(--white);font-size:16px;line-height:44px;text-align:center}
.year-select svg{position:absolute;right:18px;top:16px}
.nav-btn{position:absolute;width:145px;height:45px;color:var(--white);font-size:16px;display:flex;align-items:center;justify-content:space-between;padding:0 20px}
.nav-btn.back{left:10px;background:var(--red)}
.nav-btn.next{left:165px;background:var(--blue)}
.screen--q1 .nav-btn{top:410px}
.screen--q2 .nav-btn{top:419px}
.nav-btn .label{flex:1;text-align:center}
</style>
</head>
<body>

<svg class="ribbon" viewBox="0 0 170 150" aria-label="Revised">
  <polygon points="0,0 170,0 0,150" fill="var(--ribbon)"/>
  <text x="62" y="62" fill="#fff" font-family="Roboto,sans-serif" font-size="30" text-anchor="middle" transform="rotate(-41 62 62)">REVISED</text>
</svg>

<h1 class="page-title">TutorPath US App</h1>

<!-- Main screen -->
<section class="screen screen--main">
  <div class="status-bar"><span class="carrier">●●●○○ Skyline</span><span class="time">4:21 PM</span><span class="battery">100% <i></i></span></div>
  <div class="url-bar"><div class="url-pill">www.tutorpath.example.com
    <svg width="14" height="14" viewBox="0 0 14 14"><path d="M11.5 7a4.5 4.5 0 1 1-1.3-3.2" fill="none" stroke="#fff" stroke-width="1.6"/><path d="M11 1v3.5H7.5" fill="none" stroke="#fff" stroke-width="1.6"/></svg></div></div>

  <div class="grant-avatar" role="img" aria-label="Illustration of a graduate in a cap holding a magnifying glass"></div>
  <div class="grant-banner">Get up to $5, 645* per year in Grants<br>if you qualify</div>
  <p class="promo">Complete our <b>3-minute</b> app!</p>

  <div class="area-head">SELECT AREA OF YOUR INTEREST</div>
  <ul class="area-list">
    <li><span class="icon"><svg width="16" height="16" viewBox="0 0 16 16"><path d="M3 13l9-9M11 3l2 2" stroke="#fff" stroke-width="1.5" fill="none"/></svg></span>Art &amp; Design<svg class="chev" width="8" height="12" viewBox="0 0 8 12"><path d="M1 1l5 5-5 5" stroke="var(--blue)" stroke-width="2" fill="none"/></svg></li>
    <li><span class="icon"><svg width="16" height="16" viewBox="0 0 16 16"><rect x="2" y="5" width="12" height="8" stroke="#fff" stroke-width="1.3" fill="none"/><path d="M6 5V3h4v2" stroke="#fff" stroke-width="1.3" fill="none"/></svg></span>Business<svg class="chev" width="8" height="12" viewBox="0 0 8 12"><path d="M1 1l5 5-5 5" stroke="var(--blue)" stroke-width="2" fill="none"/></svg></li>
    <li><span class="icon"><svg width="16" height="16" viewBox="0 0 16 16"><path d="M3 13l6-6M7 3l5 5M9 2l4 4" stroke="#fff" stroke-width="1.5" fill="none"/></svg></span>Criminal Justice<svg class="chev" width="8" height="12" viewBox="0 0 8 12"><path d="M1 1l5 5-5 5" stroke="var(--blue)" stroke-width="2" fill="none"/></svg></li>
    <li><span class="icon"><svg width="18" height="16" viewBox="0 0 18 16"><text x="9" y="7" fill="#fff" font-size="6" text-anchor="middle" font-family="Roboto,sans-serif">ABC</text><text x="9" y="14" fill="#fff" font-size="6" text-anchor="middle" font-family="Roboto,sans-serif">123</text></svg></span>Education &amp; Teaching<svg class="chev" width="8" height="12" viewBox="0 0 8 12"><path d="M1 1l5 5-5 5" stroke="var(--blue)" stroke-width="2" fill="none"/></svg></li>
    <li><span class="icon"><svg width="16" height="16" viewBox="0 0 16 16"><path d="M8 2L3 14M8 2l5 12M5 10h6" stroke="#fff" stroke-width="1.4" fill="none"/></svg></span>Engineering<svg class="chev" width="8" height="12" viewBox="0 0 8 12"><path d="M1 1l5 5-5 5" stroke="var(--blue)" stroke-width="2" fill="none"/></svg></li>
    <li><span class="icon"><svg width="16" height="16" viewBox="0 0 16 16"><path d="M2 4h5l1 1 1-1h5v9H9l-1 1-1-1H2z" stroke="#fff" stroke-width="1.2" fill="none"/></svg></span>Other Courses<svg class="chev" width="8" height="12" viewBox="0 0 8 12"><path d="M1 1l5 5-5 5" stroke="var(--blue)" stroke-width="2" fill="none"/></svg></li>
  </ul>

  <nav class="toolbar">
    <svg width="14" height="22" viewBox="0 0 14 22"><path d="M11 2L3 11l8 9" stroke="#fff" stroke-width="2" fill="none"/></svg>
    <svg width="14" height="22" viewBox="0 0 14 22"><path d="M3 2l8 9-8 9" stroke="#fff" stroke-width="2" fill="none"/></svg>
    <svg width="22" height="24" viewBox="0 0 22 24"><path d="M7 9H3v13h16V9h-4M11 15V2M7 6l4-4 4 4" stroke="#fff" stroke-width="1.6" fill="none"/></svg>
    <svg width="28" height="22" viewBox="0 0 28 22"><path d="M2 3h10l2 2 2-2h10v16H16l-2 2-2-2H2zM14 5v16" stroke="#fff" stroke-width="1.6" fill="none"/></svg>
    <svg width="26" height="24" viewBox="0 0 26 24"><rect x="2" y="7" width="16" height="15" stroke="#fff" stroke-width="1.6" fill="none"/><path d="M7 7V2h17v15h-6" stroke="#fff" stroke-width="1.6" fill="none"/></svg>
  </nav>
</section>

<!-- Form step 1 -->
<section class="screen screen--q1">
  <div class="status-bar"><span class="carrier">●●●○○ Skyline</span><span class="time">4:21 PM</span><span class="battery">100% <i></i></span></div>
  <div class="url-bar"><div class="url-pill">www.tutorpath.example.com
    <svg width="14" height="14" viewBox="0 0 14 14"><path d="M11.5 7a4.5 4.5 0 1 1-1.3-3.2" fill="none" stroke="#fff" stroke-width="1.6"/><path d="M11 1v3.5H7.5" fill="none" stroke="#fff" stroke-width="1.6"/></svg></div></div>

  <div class="progress"><span class="done"></span><span></span><span></span><span></span><span></span><span></span></div>
  <div class="question">Are you currently in school?<br>If yes, what year?</div>
  <ul class="options">
    <li><span class="radio on"></span>Yes</li>
    <li><span class="radio"></span>No</li>
  </ul>
  <div class="year-select">Select Year Level
    <svg width="18" height="10" viewBox="0 0 18 10"><path d="M1 1l8 8 8-8" stroke="#fff" stroke-width="1.5" fill="none"/></svg></div>
  <div class="nav-btn back"><svg width="26" height="16" viewBox="0 0 26 16"><path d="M25 8H2M9 1L2 8l7 7" stroke="#fff" stroke-width="1.6" fill="none"/></svg><span class="label">Back</span></div>
  <div class="nav-btn next"><span class="label">Next</span><svg width="26" height="16" viewBox="0 0 26 16"><path d="M1 8h23M17 1l7 7-7 7" stroke="#fff" stroke-width="1.6" fill="none"/></svg></div>

  <nav class="toolbar">
    <svg width="14" height="22" viewBox="0 0 14 22"><path d="M11 2L3 11l8 9" stroke="#fff" stroke-width="2" fill="none"/></svg>
    <svg width="14" height="22" viewBox="0 0 14 22"><path d="M3 2l8 9-8 9" stroke="#fff" stroke-width="2" fill="none"/></svg>
    <svg width="22" height="24" viewBox="0 0 22 24"><path d="M7 9H3v13h16V9h-4M11 15V2M7 6l4-4 4 4" stroke="#fff" stroke-width="1.6" fill="none"/></svg>
    <svg width="28" height="22" viewBox="0 0 28 22"><path d="M2 3h10l2 2 2-2h10v16H16l-2 2-2-2H2zM14 5v16" stroke="#fff" stroke-width="1.6" fill="none"/></svg>
    <svg width="26" height="24" viewBox="0 0 26 24"><rect x="2" y="7" width="16" height="15" stroke="#fff" stroke-width="1.6" fill="none"/><path d="M7 7V2h17v15h-6" stroke="#fff" stroke-width="1.6" fill="none"/></svg>
  </nav>
</section>

<!-- Form step 2 -->
<section class="screen screen--q2">
  <div class="status-bar"><span class="carrier">●●●○○ Skyline</span><span class="time">4:21 PM</span><span class="battery">100% <i></i></span></div>
  <div class="url-bar"><div class="url-pill">www.tutorpath.example.com
    <svg width="14" height="14" viewBox="0 0 14 14"><path d="M11.5 7a4.5 4.5 0 1 1-1.3-3.2" fill="none" stroke="#fff" stroke-width="1.6"/><path d="M11 1v3.5H7.5" fill="none" stroke="#fff" stroke-width="1.6"/></svg></div></div>

  <div class="progress"><span class="done"></span><span class="done"></span><span></span><span></span><span></span><span></span></div>
  <div class="question">What is your question on<br>this screen?</div>
  <ul class="options">
    <li><span class="radio"></span>Option 1</li>
    <li><span class="radio on"></span>Selected Option</li>
    <li><span class="radio"></span>Option 3</li>
    <li><span class="radio"></span>Option 4</li>
  </ul>
  <div class="nav-btn back"><svg width="26" height="16" viewBox="0 0 26 16"><path d="M25 8H2M9 1L2 8l7 7" stroke="#fff" stroke-width="1.6" fill="none"/></svg><span class="label">Back</span></div>
  <div class="nav-btn next"><span class="label">Next</span><svg width="26" height="16" viewBox="0 0 26 16"><path d="M1 8h23M17 1l7 7-7 7" stroke="#fff" stroke-width="1.6" fill="none"/></svg></div>

  <nav class="toolbar">
    <svg width="14" height="22" viewBox="0 0 14 22"><path d="M11 2L3 11l8 9" stroke="#fff" stroke-width="2" fill="none"/></svg>
    <svg width="14" height="22" viewBox="0 0 14 22"><path d="M3 2l8 9-8 9" stroke="#fff" stroke-width="2" fill="none"/></svg>
    <svg width="22" height="24" viewBox="0 0 22 24"><path d="M7 9H3v13h16V9h-4M11 15V2M7 6l4-4 4 4" stroke="#fff" stroke-width="1.6" fill="none"/></svg>
    <svg width="28" height="22" viewBox="0 0 28 22"><path d="M2 3h10l2 2 2-2h10v16H16l-2 2-2-2H2zM14 5v16" stroke="#fff" stroke-width="1.6" fill="none"/></svg>
    <svg width="26" height="24" viewBox="0 0 26 24"><rect x="2" y="7" width="16" height="15" stroke="#fff" stroke-width="1.6" fill="none"/><path d="M7 7V2h17v15h-6" stroke="#fff" stroke-width="1.6" fill="none"/></svg>
  </nav>
</section>

<div class="caption">
  <h2>Main Screen &amp; Form Screens</h2>
  <p>Glass &amp; Flat Style</p>
</div>

</body>
</html>
```